Varnick Fundraising E-mail Campaign

I intend to use Constant Contact to send donors 4 separate e-mail messages with pictures, text and a hot link, “Give to Restore Marlowe.” E-mails will spaced about 3 days apart. I would like the first e-mail to go out on Monday, December 17. The e-mail campaign is part of a board match annual appeal fundraising campaign for a not for profit sleep away Christian camp. Our hope is to raise $40,000.00+

Target Market(s)

Members in Constant Contact list

Colors

Designer to choose colors to be used in the design.

Requirements
Must have
• E- mail recipient must be able to access hot link

```html
<!DOCTYPE html>
<html lang="en">
<head>
<meta charset="utf-8">
<title>Varnick – Give to Restore Marlowe</title>
<link href="https://fonts.googleapis.com/css2?family=Arimo:wght@400;700&display=swap" rel="stylesheet">
<style>
:root{
  --page:#accb87;
  --paper:#ffffff;
  --teal:#0b7a56;
  --frame:#159b7b;
  --coral:#f4474f;
  --alert:#e5242a;
  --crimson:#cf1a43;
  --hill:#0ea548;
  --hill-dark:#067a3a;
  --water:#22b0dd;
}
*{margin:0;padding:0;box-sizing:border-box}
html,body{width:1200px;height:859px;overflow:hidden}
body{background:var(--page);font-family:"Arimo",Arial,sans-serif;position:relative}
.email{position:absolute;left:379px;top:16px;width:443px;height:827px;background:var(--paper);overflow:hidden}
.abs{position:absolute}
.header{left:0;top:0;width:443px;height:66px}
.header-scene{left:2px;top:8px;width:122px;height:56px;background:linear-gradient(180deg,#e9f4e0 0%,#1aa04c 60%,#22b0dd 100%)}
.brand{left:132px;top:10px;width:130px;color:var(--teal);font-weight:400;line-height:1}
.brand-name{font-size:26px;letter-spacing:0}
.brand-sub{font-size:9.6px;line-height:12px;margin-top:4px;white-space:nowrap}
.header-art{left:270px;top:2px;width:156px;height:62px;background:linear-gradient(90deg,#8f7ee6,#8fd1a0,#f2e36a,#f59a4f,#ef5b58,#c67fd1)}
.hero{left:0;top:67px;width:443px;height:201px;background:linear-gradient(160deg,#5e7d3e 0%,#9bb3a8 45%,#38402e 100%)}
.hero-frame{left:14px;top:0;width:415px;height:190px;border:2px solid #c6dd9c;border-top:0}
.cta{left:0;top:268px;width:443px;height:85px;background:var(--coral);color:#fff;text-align:center;font-weight:700;font-size:15.5px}
.cta p{position:absolute;left:0;width:100%}
.cta a{color:#fff}
.cta-rule{left:72px;top:73px;width:298px;height:1px;background:#fff}
.intro{left:8px;top:366px;width:427px;font-size:10.5px;line-height:15px;color:var(--teal);text-align:justify}
.portrait{left:5px;top:463px;width:140px;height:146px;border:3px solid var(--frame);background:linear-gradient(135deg,#cfc8c0,#c23a36 45%,#3b3b3b 100%)}
.match{left:155px;top:463px;width:270px;font-size:9.2px;line-height:10.6px;color:var(--teal)}
.gifts{left:155px;top:514px;width:280px;font-size:9.2px;line-height:10.6px;color:var(--teal);list-style:circle;padding-left:33px}
.urge{left:163px;top:609px;font-size:12.7px;color:var(--alert)}
.visit{left:0;top:648px;width:443px;text-align:center;font-size:11.4px;color:var(--crimson)}
.visit a{color:var(--crimson)}
.contact{left:8px;top:686px;font-size:9.3px;line-height:12.8px;color:var(--teal);font-style:normal}
.footer-scene{left:0;top:750px;width:443px;height:77px;background:linear-gradient(180deg,#0a9a46 0%,#0ea548 70%,#22b0dd 85%,#22b0dd 100%)}
.footer-tree{left:241px;top:674px;width:105px;height:76px;background:linear-gradient(180deg,#d7ecb8 0%,#5fbf6a 60%,#0a9a46 100%)}
</style>
</head>
<body>
<main class="email">
  <header class="abs header">
    <div class="abs header-scene" role="img" aria-label="Illustrated lakeside landscape with a tree"></div>
    <div class="abs brand">
      <div class="brand-name">VARNICK</div>
      <div class="brand-sub">PRESBYTERIAN CAMP<br>&amp; CONFERENCE CENTER</div>
    </div>
    <div class="abs header-art" role="img" aria-label="Illustration of colourful raised hands"></div>
  </header>

  <div class="abs hero" role="img" aria-label="Photo of three children crouching by a forest stream">
    <div class="abs hero-frame"></div>
  </div>

  <section class="abs cta">
    <p style="top:19px">Visit&nbsp; <a href="http://varnickcamp.org/support"><i>http://varnickcamp.org/support</i></a></p>
    <p style="top:47px">and click on&nbsp; "<a href="http://varnickcamp.org/support">Restore Marlowe</a>"</p>
    <div class="abs cta-rule"></div>
  </section>

  <p class="abs intro">A revitalized Marlowe Lake can do so much for children like Lucy. Research shows that playing outdoors will (1) enhance Lucy's ability to learn, (2) stimulates Lucy's creativity, (3) increases Lucy's sense of well-being and (4) improve Lucy's social skills.&nbsp; Research also shows that youth who attend Christian summer camp grow to interpret all of life through a lens of faith.</p>

  <div class="abs portrait" role="img" aria-label="Photo of two smiling girls at camp"></div>

  <p class="abs match">You can help us provide Lucy and children like her by taking advantage of the Revitalize Camp Marlowe Lake Matching Challenge</p>

  <ul class="abs gifts">
    <li>$100.00 will buy: material for a picnic table</li>
    <li>$250.00 will buy: materials to improve the tent frames</li>
    <li>$500.00 will buy: materials to repair the bath house roof</li>
    <li>$1,000.00 will buy: a new tent to replace one damaged by tornado</li>
    <li>$5,000.00 will buy: half the roofing material for Marlowe Dining Hall</li>
  </ul>

  <p class="abs urge">If you haven't done so, please donate today.</p>

  <p class="abs visit">Visit&nbsp; <a href="http://varnickcamp.org/support">http://varnickcamp.org/support</a> and click on&nbsp; "Restore Marlowe"</p>

  <div class="abs footer-tree" role="img" aria-label="Illustration of a leafy tree on a hill"></div>
  <div class="abs footer-scene" role="img" aria-label="Illustration of green rolling hills beside a lake"></div>

  <address class="abs contact">
    Contact:<br>
    60 Marlowe Lake Road Varnick, NY 12540<br>
    Phone: 555-010-6383 Fax: 555-010-7824<br>
    E-Mail: office@varnickcamp.org
  </address>
</main>
</body>
</html>
```